Unique Business Card Design

Unique Business Card design for our orthotic and prosthetic company. Our logo is on our website, color is light blue. Unique shape (artificial leg shaped, vertical, etc..) preferred. Logo, business name, individual name and basic demographics needed.

Industry/Entity Type

Business

Contact Information for Business Card

Logo, Industry, Phone # Logo, "Prosthetic & Orthotic Services" Place to add individual name and contact info

Colors
cee9f5

Requirements
Must have
• The icon must be there, placement of "Prosthetic & Orthotic Services" can be moved
Nice to have
• Like the mix of light blue, and a little darker blue. One design included the icons from my website which was a nice touch

```html
<!DOCTYPE html>
<html lang="en">
<head>
<meta charset="utf-8">
<title>Limbwell Inc. Business Card</title>
<link rel="stylesheet" href="https://fonts.googleapis.com/css2?family=Source+Sans+3:wght@400;600;700&display=swap">
<style>
  :root {
    --brand-blue: #1560ad;
    --ink-grey: #4a4a4a;
    --card-white: #ffffff;
    --backdrop: #5b4b3c;
    --font-main: "Source Sans 3", "Helvetica Neue", Arial, sans-serif;
  }
  html, body {
    margin: 0;
    padding: 0;
    width: 1200px;
    height: 987px;
    overflow: hidden;
    background: var(--backdrop);
    font-family: var(--font-main);
  }
  .canvas { position: relative; width: 1200px; height: 987px; }
  .card {
    position: absolute;
    left: 293px;
    width: 615px;
    height: 352px;
    border-radius: 18px;
    overflow: hidden;
  }
  .card--front { top: 130px; background: var(--card-white); }
  .card--back { top: 506px; background: var(--brand-blue); }

  /* Front side */
  .front-tab {
    position: absolute; left: 0; top: 38px;
    width: 52px; height: 76px;
    background: var(--brand-blue);
  }
  .front-mark {
    position: absolute; left: 22px; top: 35px;
    width: 78px; height: 78px; border-radius: 50%;
    background: var(--brand-blue);
    border: 3px solid var(--card-white);
    box-sizing: border-box;
  }
  .front-wordmark {
    position: absolute; left: 124px; top: 44px;
    font-size: 25px; font-weight: 600; letter-spacing: 0.3px;
    color: var(--brand-blue); line-height: 1;
  }
  .front-rule {
    position: absolute; left: 129px; top: 76px;
    width: 197px; height: 2px; background: var(--brand-blue);
  }
  .front-tagline {
    position: absolute; left: 136px; top: 82px;
    font-size: 13px; color: var(--brand-blue);
  }
  .person-name {
    position: absolute; left: 122px; top: 162px;
    font-size: 22px; font-weight: 600; color: var(--brand-blue);
  }
  .person-title {
    position: absolute; left: 122px; top: 192px;
    font-size: 14px; font-weight: 600; color: var(--brand-blue);
  }
  .contact-list {
    position: absolute; left: 122px; top: 232px;
    margin: 0; padding: 0; list-style: none;
    font-size: 15px; line-height: 23.5px; color: var(--ink-grey);
  }
  .contact-list b { color: var(--brand-blue); font-weight: 700; }
  .contact-divider {
    position: absolute; left: 344px; top: 236px;
    width: 1px; height: 82px; background: var(--brand-blue);
  }
  .address-block {
    position: absolute; left: 357px; top: 256px;
    font-size: 15px; line-height: 22px; color: var(--ink-grey);
  }
  .address-block .web { color: var(--brand-blue); }

  /* Back side */
  .back-mark {
    position: absolute; left: 94px; top: 118px;
    width: 112px; height: 112px; border-radius: 50%;
    background: var(--card-white);
  }
  .back-wordmark {
    position: absolute; left: 234px; top: 134px;
    font-size: 35px; font-weight: 600; letter-spacing: 0.3px;
    color: var(--card-white); line-height: 1;
  }
  .back-rule {
    position: absolute; left: 237px; top: 172px;
    width: 282px; height: 6px; background: var(--card-white);
  }
  .back-tagline {
    position: absolute; left: 250px; top: 182px;
    font-size: 18px; color: var(--card-white);
  }
  .back-web {
    position: absolute; left: 0; right: 0; top: 300px;
    display: flex; align-items: center; justify-content: center; gap: 8px;
    font-size: 15px; color: var(--card-white);
  }
  .back-web .line {
    width: 122px; height: 1px;
    background: linear-gradient(to right, rgba(255,255,255,0), #ffffff);
  }
  .back-web .line--right {
    background: linear-gradient(to left, rgba(255,255,255,0), #ffffff);
  }
</style>
</head>
<body>
<main class="canvas">
  <section class="card card--front" aria-label="Card front">
    <div class="front-tab"></div>
    <div class="front-mark"></div>
    <div class="front-wordmark">LIMBWELL INC.</div>
    <div class="front-rule"></div>
    <div class="front-tagline">Prosthetic &amp; Orthotic Services</div>

    <div class="person-name">Marlo Tevis</div>
    <div class="person-title">CO LPO</div>

    <ul class="contact-list">
      <li><b>P :</b> 555.210.4400</li>
      <li><b>M :</b> 555.210.4417</li>
      <li><b>F :</b> 555-3308142</li>
      <li>Mtevis@limbwellinc.com</li>
    </ul>
    <div class="contact-divider"></div>
    <div class="address-block">
      2290 W. 14th St.<br>
      Brooklyn, NY 11223<br>
      <span class="web">www.limbwellinc.com</span>
    </div>
  </section>

  <section class="card card--back" aria-label="Card back">
    <div class="back-mark"></div>
    <div class="back-wordmark">LIMBWELL INC.</div>
    <div class="back-rule"></div>
    <div class="back-tagline">Prosthetic &amp; Orthotic Services</div>
    <div class="back-web">
      <span class="line"></span>
      <span>www.limbwellinc.com</span>
      <span class="line line--right"></span>
    </div>
  </section>
</main>
</body>
</html>
```